Word Templates for Green Energy Consulting Company

Please see attached brief. This is what we'd like. Please note that we have also launched a PowerPoint template project and we want the two designs to be consistent. We encourage designers to submit to both contests. PowerPoint project is here: https://www.plumvexa.com/manage-project/brief/7381526

Font styles to use
Serif
Sans Serif

```html
<!DOCTYPE html>
<html lang="en">
<head>
<meta charset="utf-8">
<title>Norvale Group – Word Template Set</title>
<link href="https://fonts.googleapis.com/css2?family=Arimo:ital,wght@0,400;0,700;1,400&family=Montserrat:wght@300;400;500;600;700&display=swap" rel="stylesheet">
<style>
  :root{
    --navy:#203348;
    --navy-deep:#1b2a3d;
    --blue:#1687C3;
    --blue-mid:#1A567D;
    --green:#6DB044;
    --green-mid:#4C9944;
    --green-dark:#207A3D;
    --ink:#231F20;
    --text:#3a3a3a;
    --board:#c9c9cb;
    --white:#ffffff;
  }
  *{margin:0;padding:0;box-sizing:border-box}
  html,body{width:1200px;height:3128px;overflow:hidden}
  body{background:var(--board);position:relative;font-family:"Montserrat",Arial,sans-serif;color:var(--text)}

  .page{position:absolute;width:486px;background:var(--white);overflow:hidden}
  .cover{height:685px}
  .sheet{height:688px}
  .shadow{position:absolute;width:486px;height:14px;background:linear-gradient(#8e8e90,rgba(201,201,203,0))}

  .page svg.art{position:absolute;left:0;top:0}

  /* cover one */
  .cover-one .slogan{position:absolute;top:294px;left:0;width:100%;text-align:center;font-family:"Montserrat",sans-serif;font-weight:600;font-size:32px;line-height:40px;color:var(--blue-mid);letter-spacing:.5px}
  .cover-one .slogan span{color:var(--green-mid);font-weight:700}
  .brand{font-family:"Montserrat",sans-serif;font-weight:700;color:var(--navy);text-align:center;white-space:nowrap}
  .cover-one .brand{position:absolute;top:500px;left:0;width:100%;font-size:19px;line-height:24px}
  .tagline{display:flex;align-items:center;justify-content:center;gap:6px;font-family:"Montserrat",sans-serif;color:var(--green-dark);font-weight:400;white-space:nowrap}
  .tagline i{display:block;height:1px;background:var(--green-dark)}
  .cover-one .tagline{position:absolute;top:526px;left:0;width:100%;font-size:7px;line-height:10px}
  .cover-one .tagline i{width:30px}
  .contact{position:absolute;left:0;width:100%;text-align:center;font-family:"Montserrat",sans-serif;letter-spacing:1px;white-space:nowrap}
  .contact.phone{top:618px;font-size:9px;line-height:12px;color:var(--green)}
  .contact.mail{top:633px;font-size:9.5px;line-height:12px;color:var(--white)}
  .contact.web{top:648px;font-size:12px;line-height:15px;color:var(--green);font-weight:500}

  /* cover two */
  .report-title{position:absolute;left:120px;top:44px;width:243px;height:142px;border:3px solid var(--green);border-radius:10px;text-align:center;color:var(--white);font-family:"Montserrat",sans-serif;font-weight:500;font-size:46px;line-height:52px;padding-top:6px}
  .report-title .year{position:absolute;left:50%;bottom:-26px;transform:translateX(-50%);padding:0 8px;background:#22496c;color:var(--green);font-weight:700;font-size:44px;line-height:48px}
  .cover-two .brand{position:absolute;top:368px;left:0;width:100%;font-size:36px;line-height:42px}
  .cover-two .tagline{position:absolute;top:414px;left:0;width:100%;font-size:15px;line-height:18px;color:var(--green-dark)}
  .cover-two .tagline i{width:50px}
  .cover-two .site{position:absolute;top:660px;left:0;width:100%;text-align:center;color:var(--white);font-size:9px;letter-spacing:4px}

  /* running header and footer */
  .top-strip{position:absolute;left:0;top:0;width:100%;height:19px;background:linear-gradient(90deg,#1c3550,#2b5477 40%,#223d59 70%,#1d3a52)}
  .top-rule{position:absolute;left:0;top:19px;width:100%;height:3px;background:var(--green-mid)}
  .footer{position:absolute;left:0;bottom:0;width:486px;height:70px}
  .footer .foot-brand{position:absolute;left:21px;top:34px;font-family:"Montserrat",sans-serif;font-weight:700;font-size:11.5px;color:var(--navy)}
  .footer .foot-site{position:absolute;left:285px;top:35px;font-size:8.5px;letter-spacing:1px;color:var(--navy)}

  /* text content */
  .content{position:absolute;left:19px;right:22px;top:53px}
  .content h2{font-family:"Arimo",Arial,sans-serif;font-weight:700;font-size:15.5px;line-height:19px;color:var(--green-mid)}
  .content .sub{font-family:"Arimo",Arial,sans-serif;font-size:10.5px;line-height:14px;color:var(--blue-mid);margin-bottom:7px}
  .content .sub.bold{font-weight:700;color:var(--navy)}
  .content p{font-family:"Montserrat",sans-serif;font-weight:400;font-size:7.1px;line-height:15.6px;color:var(--text);text-align:justify;margin-bottom:15px}
  .content .level{font-family:"Arimo",Arial,sans-serif;font-style:italic;font-size:10px;line-height:16px;color:var(--blue-mid)}
  .content section{margin-bottom:6px}

  .split{display:flex;gap:14px}
  .split .col{width:333px}
  .photo{flex:none;width:187px;height:212px;background:linear-gradient(170deg,#dfeaf3 0%,#c8dbe8 35%,#a9bf9a 75%,#7f9a6d 100%)}

  /* table of contents */
  .toc-title{position:absolute;left:25px;top:53px;font-family:"Arimo",Arial,sans-serif;font-weight:700;font-size:15px;line-height:17px}
  .toc-title .a{color:var(--green-mid)}
  .toc-title .b{color:var(--navy)}
  .toc{position:absolute;left:25px;top:101px;list-style:none}
  .toc li{display:flex;align-items:center;height:22px;margin-bottom:19px}
  .toc .num{width:21px;height:22px;background:var(--green-mid);color:var(--white);font-family:"Arimo",sans-serif;font-weight:700;font-size:9px;display:flex;align-items:center;justify-content:center}
  .toc .bar{width:384px;height:22px;margin-left:5px;background:var(--navy);color:var(--white);font-family:"Arimo",sans-serif;font-weight:700;font-size:10.5px;display:flex;align-items:center;padding-left:12px;letter-spacing:.3px}
  .toc .pg{width:21px;height:22px;margin-left:4px;background:var(--green-mid);color:var(--white);font-family:"Arimo",sans-serif;font-weight:700;font-size:9px;display:flex;align-items:center;justify-content:center}

  /* style guide */
  .spec{position:absolute;left:19px;top:53px}
  .spec .h18{font-family:"Arimo",sans-serif;font-weight:700;font-size:15.5px;line-height:19px;color:var(--green-mid)}
  .spec .h12{font-family:"Arimo",sans-serif;font-weight:700;font-size:10.5px;line-height:15px;color:var(--navy)}
  .spec .ob{font-family:"Arimo",sans-serif;font-style:italic;font-size:10.5px;line-height:15px;color:var(--blue-mid);margin-top:8px}
  .spec .lt{font-family:"Montserrat",sans-serif;font-weight:300;font-size:7px;line-height:12px;color:var(--ink)}
  .swatch{position:absolute;width:72px;height:60px;color:var(--white);font-size:6.5px;display:flex;align-items:center;justify-content:center;font-family:"Montserrat",sans-serif}
  .cmyk{position:absolute;display:grid;grid-template-columns:20px 16px 20px;font-size:8.5px;line-height:13.5px;font-family:"Montserrat",sans-serif}
  .cmyk .v1{text-align:right;padding-right:4px}
  .cmyk .k{color:var(--navy);text-align:center}
  .cmyk .v2{color:var(--navy);padding-left:3px}
</style>
</head>
<body>

<!-- Cover: slogan -->
<div class="page cover cover-one" style="left:87px;top:94px">
  <svg class="art" width="486" height="685" viewBox="0 0 486 685" aria-hidden="true">
    <defs>
      <linearGradient id="topNavy" x1="0" y1="0" x2="1" y2="0">
        <stop offset="0" stop-color="#1d2f45"/><stop offset="1" stop-color="#233f5c"/>
      </linearGradient>
      <linearGradient id="baseBlue" x1="0" y1="0" x2="1" y2="0">
        <stop offset="0" stop-color="#1d7db8"/><stop offset="0.55" stop-color="#1e4f7a"/><stop offset="1" stop-color="#203348"/>
      </linearGradient>
    </defs>
    <polygon points="0,0 486,0 486,230 0,141" fill="url(#topNavy)"/>
    <polygon points="0,141 486,230 486,238 0,147" fill="#4C9944"/>
    <path d="M0,597 L72,597 L72,640 C190,562 360,518 486,546 L486,685 L0,685 Z" fill="url(#baseBlue)"/>
  </svg>
  <div class="slogan">THE SPARK<br>OF <span>CLEAN THINKING</span></div>
  <div class="brand">Norvale Group</div>
  <div class="tagline"><i></i>The Spark of Clean Thinking<i></i></div>
  <div class="contact phone">555-014-2283</div>
  <div class="contact mail">info@norvalegroup.com</div>
  <div class="contact web">www.norvalegroup.com</div>
</div>

<!-- Cover: annual report -->
<div class="page cover cover-two" style="left:640px;top:94px">
  <svg class="art" width="486" height="685" viewBox="0 0 486 685" aria-hidden="true">
    <defs>
      <linearGradient id="reportTop" x1="0" y1="0" x2="1" y2="0">
        <stop offset="0" stop-color="#1f3a58"/><stop offset="1" stop-color="#24618f"/>
      </linearGradient>
      <linearGradient id="reportBase" x1="0" y1="0" x2="1" y2="0">
        <stop offset="0" stop-color="#1d3350"/><stop offset="1" stop-color="#1c5f93"/>
      </linearGradient>
      <linearGradient id="spine" x1="0" y1="0" x2="1" y2="0">
        <stop offset="0" stop-color="#000" stop-opacity=".28"/><stop offset="0.5" stop-color="#000" stop-opacity=".06"/><stop offset="1" stop-color="#000" stop-opacity="0"/>
      </linearGradient>
    </defs>
    <path d="M0,0 H486 V228 L243,278 L0,228 Z" fill="url(#reportTop)"/>
    <path d="M0,228 L243,278 L486,228 V236 L243,286 L0,236 Z" fill="#4C9944"/>
    <path d="M0,640 C160,690 360,650 440,532 L440,583 L486,583 L486,685 L0,685 Z" fill="url(#reportBase)"/>
    <path d="M0,606 C140,648 300,620 382,500 L316,500 L316,447 L486,447 L486,583 L440,583 L440,532 C360,650 160,690 0,640 Z" fill="#6DB044"/>
    <rect x="0" y="0" width="90" height="685" fill="url(#spine)"/>
  </svg>
  <div class="report-title">ANNUAL<br>REPORT<span class="year">2023</span></div>
  <div class="brand">Norvale Group</div>
  <div class="tagline"><i></i>The Spark of Clean Thinking<i></i></div>
  <div class="site">www.norvalegroup.com</div>
</div>

<!-- Running footer graphic used on inner pages -->
<svg width="0" height="0" style="position:absolute" aria-hidden="true">
  <defs>
    <linearGradient id="footBand" x1="0" y1="0" x2="1" y2="0">
      <stop offset="0" stop-color="#1687C3"/><stop offset="0.6" stop-color="#1A567D"/><stop offset="1" stop-color="#203348"/>
    </linearGradient>
    <g id="footArt">
      <rect x="0" y="56" width="486" height="14" fill="url(#footBand)"/>
      <path d="M300,60 C370,58 416,44 438,22 L426,22 L426,9 L486,9 L486,70 L466,70 L466,36 C430,62 380,66 300,66 Z" fill="#4C9944"/>
    </g>
  </defs>
</svg>

<!-- Table of contents -->
<div class="page sheet" style="left:87px;top:870px">
  <div class="top-strip" role="img" aria-label="Dark blue photographic header strip"></div>
  <div class="top-rule"></div>
  <div class="toc-title"><div class="a">TABLE</div><div class="b">OF CONTENT</div></div>
  <ol class="toc">
    <li><span class="num">1</span><span class="bar">HEADING GOES HERE</span><span class="pg">01</span></li>
    <li><span class="num">2</span><span class="bar">HEADING GOES HERE</span><span class="pg">02</span></li>
    <li><span class="num">3</span><span class="bar">HEADING GOES HERE</span><span class="pg">03</span></li>
    <li><span class="num">4</span><span class="bar">HEADING GOES HERE</span><span class="pg">04</span></li>
    <li><span class="num">5</span><span class="bar">HEADING GOES HERE</span><span class="pg">05</span></li>
    <li><span class="num">6</span><span class="bar">HEADING GOES HERE</span><span class="pg">06</span></li>
    <li><span class="num">7</span><span class="bar">HEADING GOES HERE</span><span class="pg">07</span></li>
    <li><span class="num">8</span><span class="bar">HEADING GOES HERE</span><span class="pg">08</span></li>
    <li><span class="num">9</span><span class="bar">HEADING GOES HERE</span><span class="pg">09</span></li>
  </ol>
  <div class="footer">
    <svg width="486" height="70" viewBox="0 0 486 70" aria-hidden="true"><use href="#footArt"/></svg>
    <div class="foot-brand">Norvale Group</div>
    <div class="foot-site">www.norvalegroup.com</div>
  </div>
</div>
<div class="shadow" style="left:87px;top:1558px"></div>

<!-- Text page: three sections -->
<div class="page sheet" style="left:640px;top:870px">
  <div class="top-strip" role="img" aria-label="Dark blue photographic header strip"></div>
  <div class="top-rule"></div>
  <div class="content">
    <section>
      <h2>HEADING GOES HERE</h2>
      <div class="sub">SUBTITLE GOES HERE</div>
      <p>Lorem ipsum dolor sit amet, consectetuer adipiscing elit, sed diam nonummy nibh euismod tincidunt ut laoreet dolore magna aliquam erat volutpat. Ut wisi enim ad minim veniam, quis nostrud exerci tation ullamcorper suscipit lobortis nisl ut aliquip ex ea commodo consequat. Duis autem vel eum iriure dolor in hendrerit in vulputate velit esse molestie consequat, vel illum dolore eu feugiat nulla facilisis at vero eros et accumsan et iusto odio dignissim qui blandit praesent luptatum zzril delenit augue duis dolore te feugait nulla facilisi.</p>
      <p>Lorem ipsum dolor sit amet, cons ectetuer adipiscing elit, sed diam nonummy nibh euismod tincidunt ut laoreet dolore magna aliquam erat volutpat. Ut wisi enim ad minim veniam, quis nostrud exerci tation ullamcorper suscipit lobortis nisl ut aliquip ex ea commodo consequat.</p>
    </section>
    <section>
      <h2>HEADING GOES HERE</h2>
      <div class="sub">SUBTITLE GOES HERE</div>
      <p>Lorem ipsum dolor sit amet, consectetuer adipiscing elit, sed diam nonummy nibh euismod tincidunt ut laoreet dolore magna aliquam erat volutpat. Ut wisi enim ad minim veniam, quis nostrud exerci tation ullamcorper suscipit lobortis nisl ut aliquip ex ea commodo consequat. Duis autem vel eum iriure dolor in hendrerit in vulputate velit esse molestie consequat, vel illum dolore eu feugiat nulla facilisis at vero eros et accumsan et iusto odio dignissim qui blandit praesent luptatum zzril delenit augue duis dolore te feugait nulla facilisi.</p>
      <p>Lorem ipsum dolor sit amet, cons ectetuer adipiscing elit, sed diam nonummy nibh euismod tincidunt ut laoreet dolore magna aliquam erat volutpat. Ut wisi enim ad minim veniam, quis nostrud exerci tation ullamcorper suscipit lobortis nisl ut aliquip ex ea commodo consequat.</p>
    </section>
    <section>
      <h2>HEADING GOES HERE</h2>
      <div class="sub">SUBTITLE GOES HERE</div>
      <p>Lorem ipsum dolor sit amet, consectetuer adipiscing elit, sed diam nonummy nibh euismod tincidunt ut laoreet dolore magna aliquam erat volutpat. Ut wisi enim ad minim veniam, quis nostrud exerci tation ullamcorper suscipit lobortis nisl ut aliquip ex ea commodo consequat. Duis autem vel eum iriure dolor in hendrerit in vulputate velit esse molestie consequat, vel illum dolore eu feugiat nulla facilisis at vero eros et accumsan et iusto odio dignissim qui blandit praesent luptatum zzril delenit augue duis dolore te feugait nulla facilisi.</p>
      <p>Lorem ipsum dolor sit amet, cons ectetuer adipiscing elit, sed diam nonummy nibh euismod tincidunt ut laoreet dolore magna aliquam erat volutpat. Ut wisi enim ad minim veniam, quis nostrud exerci tation ullamcorper suscipit lobortis nisl ut aliquip ex ea commodo consequat.</p>
    </section>
  </div>
  <div class="footer">
    <svg width="486" height="70" viewBox="0 0 486 70" aria-hidden="true"><use href="#footArt"/></svg>
    <div class="foot-brand">Norvale Group</div>
    <div class="foot-site">www.norvalegroup.com</div>
  </div>
</div>
<div class="shadow" style="left:640px;top:1558px"></div>

<!-- Text page with photo -->
<div class="page sheet" style="left:87px;top:1619px">
  <div class="top-strip" role="img" aria-label="Dark blue photographic header strip"></div>
  <div class="top-rule"></div>
  <div class="content">
    <section>
      <h2>HEADING GOES HERE</h2>
      <div class="sub">SUBTITLE GOES HERE</div>
      <p>Lorem ipsum dolor sit amet, consectetuer adipiscing elit, sed diam nonummy nibh euismod tincidunt ut laoreet dolore magna aliquam erat volutpat. Ut wisi enim ad minim veniam, quis nostrud exerci tation ullamcorper suscipit lobortis nisl ut aliquip ex ea commodo consequat. Duis autem vel eum iriure dolor in hendrerit in vulputate velit esse molestie consequat, vel illum dolore eu feugiat nulla facilisis at vero eros et accumsan et iusto odio dignissim qui blandit praesent luptatum zzril delenit augue duis dolore te feugait nulla facilisi.</p>
      <p>Lorem ipsum dolor sit amet, cons ectetuer adipiscing elit, sed diam nonummy nibh euismod tincidunt ut laoreet dolore magna aliquam erat volutpat. Ut wisi enim ad minim veniam, quis nostrud exerci tation ullamcorper suscipit lobortis nisl ut aliquip ex ea commodo consequat.</p>
      <p>Lorem ipsum dolor sit amet, consectetuer adipiscing elit, sed diam nonummy nibh euismod tincidunt ut laoreet dolore magna aliquam erat volutpat. Ut wisi enim ad minim veniam, quis nostrud exerci tation ullamcorper suscipit lobortis nisl ut aliquip ex ea commodo consequat. Duis autem vel eum iriure dolor in hendrerit in vulputate velit esse molestie consequat, vel illum dolore eu feugiat nulla facilisis at vero eros et accumsan et iusto odio dignissim qui blandit praesent luptatum zzril delenit augue duis dolore te feugait nulla facilisi.</p>
    </section>
    <section>
      <h2>HEADING GOES HERE</h2>
      <div class="sub">SUBTITLE GOES HERE</div>
      <div class="split">
        <div class="col">
          <p>Lorem ipsum dolor sit amet, consectetuer adipiscing elit, sed diam nonummy nibh euismod tincidunt ut laoreet dolore magna aliquam erat volutpat. Ut wisi enim ad minim veniam, quis nostrud exerci tation ullamcorper suscipit lobortis nisl ut aliquip ex ea commodo consequat. Duis autem vel eum iriure dolor in hendrerit in vulputate velit esse molestie consequat, vel illum dolore eu feugiat nulla facilisis at vero eros et accumsan et iusto odio dignissim qui blandit praesent luptatum zzril delenit augue duis dolore te feugait nulla facilisi.</p>
          <p>Lorem ipsum dolor sit amet, cons ectetuer adipiscing elit, sed diam nonummy nibh euismod tincidunt ut laoreet dolore magna aliquam erat volutpat. Ut wisi enim ad minim veniam, quis nostrud exerci tation ullamcorper suscipit lobortis nisl ut aliquip ex ea commodo consequat.</p>
        </div>
        <div class="photo" role="img" aria-label="Photo of raised hands holding light bulbs against a bright sky"></div>
      </div>
    </section>
  </div>
  <div class="footer">
    <svg width="486" height="70" viewBox="0 0 486 70" aria-hidden="true"><use href="#footArt"/></svg>
    <div class="foot-brand">Norvale Group</div>
    <div class="foot-site">www.norvalegroup.com</div>
  </div>
</div>
<div class="shadow" style="left:87px;top:2307px"></div>

<!-- Text page with heading levels -->
<div class="page sheet" style="left:640px;top:1619px">
  <div class="top-strip" role="img" aria-label="Dark blue photographic header strip"></div>
  <div class="top-rule"></div>
  <div class="content">
    <h2>HEADING GOES HERE</h2>
    <div class="sub bold">SUBTITLE GOES HERE</div>
    <div class="level">"1." Heading 1</div>
    <p>Lorem ipsum dolor sit amet, consectetuer adipiscing elit, sed diam nonummy nibh euismod tincidunt ut laoreet dolore magna aliquam erat volutpat. Ut wisi enim ad minim veniam, quis nostrud exerci tation ullamcorper suscipit lobortis nisl ut aliquip ex ea commodo consequat. Duis autem vel eum iriure dolor in hendrerit in vulputate velit esse molestie consequat, vel illum dolore eu feugiat nulla facilisis at vero eros et accumsan et iusto odio dignissim qui blandit praesent luptatum zzril delenit augue duis dolore te feugait nulla facilisi.</p>
    <div class="level">"1.1. Heading 2</div>
    <p>Lorem ipsum dolor sit amet, consectetuer adipiscing elit, sed diam nonummy nibh euismod tincidunt ut laoreet dolore magna aliquam erat volutpat. Ut wisi enim ad minim veniam, quis nostrud exerci tation ullamcorper suscipit lobortis nisl ut aliquip ex ea commodo consequat. Duis autem vel eum iriure dolor in hendrerit in vulputate velit esse molestie consequat, vel illum dolore eu feugiat nulla facilisis at vero eros et accumsan et iusto odio dignissim qui blandit praesent luptatum zzril delenit augue duis dolore te feugait nulla facilisi.</p>
    <div class="level">"1.1.1. Heading 3</div>
    <p>Lorem ipsum dolor sit amet, consectetuer adipiscing elit, sed diam nonummy nibh euismod tincidunt ut laoreet dolore magna aliquam erat volutpat. Ut wisi enim ad minim veniam, quis nostrud exerci tation ullamcorper suscipit lobortis nisl ut aliquip ex ea commodo consequat. Duis autem vel eum iriure dolor in hendrerit in vulputate velit esse molestie consequat, vel illum dolore eu feugiat nulla facilisis at vero eros et accumsan et iusto odio dignissim qui blandit praesent luptatum zzril delenit augue duis dolore te feugait nulla facilisi.</p>
  </div>
  <div class="footer">
    <svg width="486" height="70" viewBox="0 0 486 70" aria-hidden="true"><use href="#footArt"/></svg>
    <div class="foot-brand">Norvale Group</div>
    <div class="foot-site">www.norvalegroup.com</div>
  </div>
</div>
<div class="shadow" style="left:640px;top:2307px"></div>

<!-- Style guide page -->
<div class="page sheet" style="left:87px;top:2375px">
  <div class="top-strip" role="img" aria-label="Dark blue photographic header strip"></div>
  <div class="top-rule"></div>
  <div class="spec">
    <div class="h18">HELVETICA BOLD 18</div>
    <div class="h12">HELVETICA BOLD 12</div>
    <div class="ob">Helvetica Oblique 12</div>
    <div class="lt">Montserrat Light 9</div>
  </div>

  <div class="swatch" style="left:19px;top:154px;background:linear-gradient(90deg,#207A3D,#6DB044)"></div>
  <div class="cmyk" style="left:103px;top:156px">
    <span class="v1" style="color:var(--green)">63</span><span class="k">C</span><span class="v2">85</span>
    <span class="v1" style="color:var(--green)">8</span><span class="k">M</span><span class="v2">27</span>
    <span class="v1" style="color:var(--green)">100</span><span class="k">Y</span><span class="v2">100</span>
    <span class="v1" style="color:var(--green)">0.34</span><span class="k">K</span><span class="v2">17</span>
  </div>
  <div class="swatch" style="left:191px;top:154px;background:var(--green-dark)">#207A3D</div>
  <div class="swatch" style="left:295px;top:154px;background:var(--green)">#6DB044</div>

  <div class="swatch" style="left:19px;top:230px;background:linear-gradient(90deg,#1687C3,#203348)"></div>
  <div class="cmyk" style="left:103px;top:232px">
    <span class="v1" style="color:var(--blue)">81</span><span class="k">C</span><span class="v2">90</span>
    <span class="v1" style="color:var(--blue)">36</span><span class="k">M</span><span class="v2">75</span>
    <span class="v1" style="color:var(--blue)">3.5</span><span class="k">Y</span><span class="v2">47</span>
    <span class="v1" style="color:var(--blue)">0</span><span class="k">K</span><span class="v2">44</span>
  </div>
  <div class="swatch" style="left:191px;top:230px;background:var(--navy)">#203348</div>
  <div class="swatch" style="left:295px;top:230px;background:var(--blue)">#1687C3</div>

  <div class="swatch" style="left:19px;top:311px;background:var(--green-mid)">#4C9944</div>
  <div class="swatch" style="left:19px;top:386px;background:var(--blue-mid)">#1A567D</div>
  <div class="swatch" style="left:19px;top:462px;background:var(--ink)">#231F20</div>

  <div class="footer">
    <svg width="486" height="70" viewBox="0 0 486 70" aria-hidden="true"><use href="#footArt"/></svg>
    <div class="foot-brand">Norvale Group</div>
    <div class="foot-site">www.norvalegroup.com</div>
  </div>
</div>
<div class="shadow" style="left:87px;top:3063px"></div>

</body>
</html>
```